I need a business card designed using the logo provided either vertical or horizontal......Harbourline Property Group is an Australian based real estate company that caters for the upper end of the market so the design of the business card "must reflect" the companies image!!
Colour combinations are optional but "must be realistic" and must be able to be accurately useable CMYK colours.
Please consider that any colours used "must be able to be used" and be suitable in following designs for "pull out banner signs" and "real estate signs".
The colours and the font in the attached designs are for example and other combinations are encouraged.
Target Market(s)
The High End of the Australian real estate market
Industry/Entity Type
Business
Contact Information for Business Card
Logo - Business Name - Director + Licensed Real Estate Agent - Mobile Number (Cell Phone) - Business Number - Fax - Email Address - Web address
Requirements
Must have
- Designs and colours (CMYK) that can easily be interpreted by an Australian printer.
Nice to have
- Some alternative ideas on colour and font..........the ones provided are ok and have been provided as an example but I am looking for alternative ideas
Should not have
- Loud, overly bright colours. Designs that do not reflect the professional standards of the business.
- Designs that look good on a computer monitor but can not be re-created on a printing press.............this is most important when it comes to shading etc.

```html
<!DOCTYPE html>
<html lang="en">
<head>
<meta charset="utf-8">
<title>Harbourline Property Group – Business Card</title>
<link rel="stylesheet" href="https://fonts.googleapis.com/css2?family=Michroma&family=Questrial&display=swap">
<style>
  :root {
    --backdrop: #e8e4dc;
    --card: #ffffff;
    --gold-deep: #9a7619;
    --gold: #c29d2e;
    --gold-light: #dcc06a;
    --gold-pale: #e7dcc0;
    --ink: #262626;
    --white: #ffffff;
  }
  * { margin: 0; padding: 0; box-sizing: border-box; }
  html, body {
    width: 1200px;
    height: 818px;
    overflow: hidden;
    background: var(--backdrop);
  }
  .canvas {
    position: relative;
    width: 1200px;
    height: 818px;
  }
  .business-card {
    position: absolute;
    left: 120px;
    top: 135px;
    width: 960px;
    height: 548px;
    background: var(--card);
    box-shadow: 0 12px 30px rgba(60, 45, 20, 0.18);
    overflow: hidden;
  }
  .card-art {
    position: absolute;
    inset: 0;
    width: 960px;
    height: 548px;
  }
  .brand {
    position: absolute;
    left: 395px;
    top: 78px;
    display: flex;
    align-items: center;
    gap: 22px;
  }
  .brand-mark {
    width: 46px;
    height: 46px;
    border-radius: 50%;
    background: var(--gold);
    flex: none;
  }
  .brand-name {
    font-family: "Michroma", sans-serif;
    font-size: 30px;
    line-height: 1.25;
    letter-spacing: 0.04em;
    color: var(--ink);
    text-transform: uppercase;
  }
  .contact-list {
    position: absolute;
    right: 48px;
    top: 262px;
    list-style: none;
    display: flex;
    flex-direction: column;
    align-items: flex-end;
    gap: 14px;
  }
  .contact-item {
    display: flex;
    align-items: center;
    gap: 14px;
    font-family: "Questrial", sans-serif;
    font-size: 21px;
    color: var(--ink);
  }
  .contact-icon {
    width: 24px;
    height: 24px;
    background: var(--gold);
    display: flex;
    align-items: center;
    justify-content: center;
    flex: none;
  }
  .contact-icon svg { width: 16px; height: 16px; }
  .employee {
    position: absolute;
    left: 52px;
    bottom: 54px;
    font-family: "Questrial", sans-serif;
    color: var(--white);
  }
  .employee-name {
    font-size: 30px;
    letter-spacing: 0.01em;
  }
  .employee-role {
    font-size: 20px;
    margin-top: 2px;
    padding-left: 60px;
  }
</style>
</head>
<body>
<main class="canvas">
  <section class="business-card" aria-label="Business card front">
    <svg class="card-art" viewBox="0 0 960 548" aria-hidden="true">
      <defs>
        <linearGradient id="gold-band" x1="0" y1="0" x2="1" y2="1">
          <stop offset="0" stop-color="var(--gold-deep)"/>
          <stop offset="0.55" stop-color="var(--gold)"/>
          <stop offset="1" stop-color="var(--gold-light)"/>
        </linearGradient>
      </defs>
      <path class="accent-swoosh" d="M300 0 C 300 250 380 450 470 548 L 440 548 C 350 450 282 250 282 0 Z" fill="var(--gold-pale)"/>
      <path class="gold-band" d="M0 0 L 268 0 C 268 250 340 450 425 548 L 0 548 Z" fill="url(#gold-band)"/>
    </svg>

    <div class="brand">
      <span class="brand-mark"></span>
      <p class="brand-name">Harbourline<br>Property Group</p>
    </div>

    <ul class="contact-list">
      <li class="contact-item">0412 555 019
        <span class="contact-icon">
          <svg viewBox="0 0 16 16"><path d="M4 2 L6.5 2 L7.5 5 L6 6.3 C6.8 8 8 9.2 9.7 10 L11 8.5 L14 9.5 L14 12 C14 13 13 14 12 14 C7 14 2 9 2 4 C2 3 3 2 4 2 Z" fill="var(--white)"/></svg>
        </span>
      </li>
      <li class="contact-item">hello@harbourlinegroup.au
        <span class="contact-icon">
          <svg viewBox="0 0 16 16"><rect x="2" y="4" width="12" height="8" fill="none" stroke="var(--white)" stroke-width="1.5"/><path d="M2 4 L8 9 L14 4" fill="none" stroke="var(--white)" stroke-width="1.5"/></svg>
        </span>
      </li>
      <li class="contact-item">www.harbourlinegroup.au
        <span class="contact-icon">
          <svg viewBox="0 0 16 16"><circle cx="8" cy="8" r="5.5" fill="none" stroke="var(--white)" stroke-width="1.4"/><ellipse cx="8" cy="8" rx="2.4" ry="5.5" fill="none" stroke="var(--white)" stroke-width="1.2"/><path d="M2.5 8 H13.5" stroke="var(--white)" stroke-width="1.2"/></svg>
        </span>
      </li>
      <li class="contact-item">14 Quay Street, Sydney NSW 2000
        <span class="contact-icon">
          <svg viewBox="0 0 16 16"><path d="M8 15 C8 15 3 9.5 3 6.2 A5 5 0 0 1 13 6.2 C13 9.5 8 15 8 15 Z" fill="var(--white)"/><circle cx="8" cy="6.2" r="1.8" fill="var(--gold)"/></svg>
        </span>
      </li>
    </ul>

    <div class="employee">
      <p class="employee-name">Employee Name</p>
      <p class="employee-role">Managing Director</p>
    </div>
  </section>
</main>
</body>
</html>
```